Basic business card

use my newly created logo - and the phrases (Lower Cost of Test & Accelarated New Product Introduction) - and my new email domain / ID - use at conferences / tradeshows

Industry/Entity Type

semiconductor

Contact Information for Business Card

Daniel K Forde, Owner, communicate via Logo - Lower COT - Cost of Test, Accelerated NPI - New Product Introduction, phone +1 555 613 0946, Chandler, Arizona, USA, daniel.forde@qal-vub.com

Font styles to use
Sans Serif

Requirements
Nice to have
• re-use my logo created via Pixel Harbor last August (#7315926)

```html
<!DOCTYPE html>
<html lang="en">
<head>
<meta charset="utf-8">
<title>QAL-VUB Business Card</title>
<link rel="stylesheet" href="https://fonts.googleapis.com/css2?family=Montserrat:wght@400;500;700&display=swap">
<style>
  :root {
    --bg: #e9e6e1;
    --card-light: #ffffff;
    --card-dark: #1c1c1e;
    --ink: #4a5068;
    --ink-soft: #4f535b;
    --rule: #6b6f78;
    --orange: #eea032;
    --sky: #4fbde3;
    --green: #7cb92f;
    --blue: #1a6fb3;
    --logo-dark: #d8dadd;
  }
  * { margin: 0; padding: 0; box-sizing: border-box; }
  html, body { width: 900px; height: 1200px; overflow: hidden; }
  body {
    background: var(--bg);
    font-family: "Montserrat", Arial, sans-serif;
    position: relative;
  }
  .card {
    position: absolute;
    left: 80px;
    width: 742px;
    height: 442px;
    border-radius: 32px;
    overflow: hidden;
    box-shadow: 0 6px 14px rgba(0,0,0,0.35);
  }
  .card--front { top: 130px; background: var(--card-light); }
  .card--back  { top: 638px; background: var(--card-dark); }
  .color-band {
    position: absolute;
    left: 0; right: 0; bottom: 0;
    height: 14px;
    display: flex;
  }
  .color-band span { flex: 1; }
  .color-band .orange { background: var(--orange); }
  .color-band .sky    { background: var(--sky); }
  .color-band .green  { background: var(--green); }
  .color-band .blue   { background: var(--blue); }

  .brand {
    position: absolute;
    display: flex;
    align-items: center;
    font-weight: 500;
    letter-spacing: 1px;
  }
  .brand__mark { display: block; }
  .card--front .brand {
    left: 46px; top: 208px;
    font-size: 46px;
    color: var(--ink);
  }
  .card--front .brand__mark { width: 22px; height: 22px; background: var(--ink); margin-right: 14px; }
  .card--back .brand {
    left: 100px; top: 188px;
    font-size: 70px;
    color: var(--logo-dark);
  }
  .card--back .brand__mark { width: 34px; height: 34px; background: var(--logo-dark); margin-right: 22px; }

  .divider {
    position: absolute;
    left: 394px; top: 132px;
    width: 2px; height: 188px;
    background: var(--rule);
  }
  .contact {
    position: absolute;
    left: 430px; top: 128px;
    color: var(--ink-soft);
  }
  .contact__name { font-size: 26px; font-weight: 700; color: var(--ink); line-height: 1.1; }
  .contact__role { font-size: 16px; margin-top: 2px; }
  .contact__list { list-style: none; margin-top: 18px; }
  .contact__list li {
    display: flex; align-items: center;
    font-size: 16px; height: 22px;
  }
  .contact__list svg { width: 14px; height: 14px; margin: 0 17px 0 2px; }
  .contact__address { font-size: 16px; line-height: 20px; margin-top: 20px; }
</style>
</head>
<body>
  <section class="card card--front">
    <div class="brand"><span class="brand__mark"></span>QAL-VUB</div>
    <div class="divider"></div>
    <div class="contact">
      <div class="contact__name">Daniel K Forde</div>
      <div class="contact__role">Owner</div>
      <ul class="contact__list">
        <li>
          <svg viewBox="0 0 16 16" aria-hidden="true"><path fill="#eea032" d="M3 6c0-2 2-3 5-3s5 1 5 3l-2 1-1-2H6L5 7 3 6zm1 2h8l1 5H3l1-5zm4 1.5a1.5 1.5 0 100 3 1.5 1.5 0 000-3z"/></svg>
          555-613-0946
        </li>
        <li>
          <svg viewBox="0 0 16 16" aria-hidden="true"><rect x="1" y="3" width="14" height="10" fill="#4fbde3"/><path d="M1 3l7 6 7-6" fill="none" stroke="#fff" stroke-width="1.2"/></svg>
          daniel.forde@qal-vub.com
        </li>
        <li>
          <svg viewBox="0 0 16 16" aria-hidden="true"><circle cx="8" cy="8" r="7" fill="#1a6fb3"/><path d="M4 5c2 0 2 2 4 2s1 3-1 4M10 3c0 2 2 2 3 3" fill="none" stroke="#fff" stroke-width="1.3"/></svg>
          www.qal-vub.com
        </li>
      </ul>
      <div class="contact__address">418 West Elm Ave, #112<br>Chandler, AZ 85226</div>
    </div>
    <div class="color-band"><span class="orange"></span><span class="sky"></span><span class="green"></span><span class="blue"></span></div>
  </section>

  <section class="card card--back">
    <div class="brand"><span class="brand__mark"></span>QAL-VUB</div>
    <div class="color-band"><span class="orange"></span><span class="sky"></span><span class="green"></span><span class="blue"></span></div>
  </section>
</body>
</html>
```